Business Cards

Need business card design that I can update for new employees and details. Needs to incorporate our logo, be bright and fun (in line with tourism and holidays)
Would like a Map of Western Australia on the front with locations all the caravan parks we own (just purchased Tom Price so please include that as well as others listed on our website).
Target Market(s)
Famillies
Contact Information for Business Card
5 Cards -
Neil Perrow (Director) e: perrow@wattlebay.com.au p: 0491 570 156
Mira Perrow (Director) e: perrow@wattlebay.com.au p: 0491 570 157
Owen Halvey (General Manager) e: halvey@wattlebay.com.au p: 0491 570 158
Helen Halvey (General Manager) e: halvey@wattlebay.com.au p: 0491 570 159
Colin Danby (Training and Operations Manager) - e: danby@wattlebay.com.au p:0491 570 110
Colors
Look and feel

```html
<!DOCTYPE html>
<html lang="en">
<head>
<meta charset="utf-8">
<title>Wattlebay Tourist Parks – Business Card</title>
<link rel="stylesheet" href="https://fonts.googleapis.com/css2?family=Roboto:wght@400;500;700&display=swap">
<style>
  :root {
    --teal: #3fc1ca;
    --teal-light: #5dcfd6;
    --teal-deep: #2fb3bd;
    --mint: #7fc4b1;
    --ink: #4a4d50;
    --ink-soft: #6b6e71;
    --rule: #b9bcbf;
    --paper: #f7f8f8;
    --stage: #e6e9eb;
  }
  * { box-sizing: border-box; margin: 0; padding: 0; }
  html, body {
    width: 1200px; height: 900px; overflow: hidden;
    background: var(--stage);
    font-family: "Roboto", Arial, sans-serif;
  }
  .card {
    position: absolute; left: 320px;
    width: 560px; height: 342px;
    border-radius: 3px; overflow: hidden;
    box-shadow: 0 6px 18px rgba(0,0,0,0.12);
  }

  /* Back of card */
  .card--back {
    top: 70px;
    background: linear-gradient(135deg, var(--teal-light), var(--teal) 55%, var(--teal-deep));
  }
  .back-brand {
    position: absolute; left: 0; right: 0; top: 118px;
    display: flex; align-items: center; justify-content: center; gap: 16px;
  }
  .back-brand__square {
    width: 46px; height: 46px; border: 4px solid #fff;
  }
  .back-brand__name {
    color: #fff; font-weight: 500; font-size: 30px; letter-spacing: 1px;
  }
  .back-web {
    position: absolute; left: 40px; bottom: 30px;
    color: #fff; font-size: 14px; letter-spacing: 3px;
  }

  /* Front of card */
  .card--front {
    top: 488px;
    background: var(--paper);
  }
  .front-brand {
    position: absolute; left: 36px; top: 96px; width: 218px;
    display: flex; align-items: center; gap: 12px;
  }
  .front-brand__square {
    flex: none; width: 40px; height: 40px; background: var(--mint);
  }
  .front-brand__name {
    color: var(--ink); font-weight: 400; font-size: 19px;
    letter-spacing: 2px; line-height: 1.25; text-transform: uppercase;
  }
  .divider {
    position: absolute; left: 280px; top: 70px;
    width: 1px; height: 122px; background: var(--rule);
  }
  .contact {
    position: absolute; left: 306px; top: 80px;
  }
  .contact__name {
    color: var(--teal); font-weight: 700; font-size: 24px;
    text-transform: uppercase; letter-spacing: 0.3px;
  }
  .contact__role {
    color: var(--teal); font-weight: 500; font-size: 14px;
    text-transform: uppercase; margin-top: 2px;
  }
  .contact__list { list-style: none; margin-top: 16px; }
  .contact__item {
    display: flex; align-items: center; gap: 9px;
    color: var(--ink); font-size: 15px; line-height: 24px;
  }
  .contact__icon { width: 13px; height: 13px; flex: none; }
  .front-band { position: absolute; left: 0; bottom: 0; }
  .front-web {
    position: absolute; right: 26px; bottom: 18px;
    color: #fff; font-size: 16px; letter-spacing: 2.5px;
  }
</style>
</head>
<body>

<section class="card card--back" aria-label="Business card back">
  <div class="back-brand">
    <span class="back-brand__square"></span>
    <span class="back-brand__name">Wattlebay Tourist Parks</span>
  </div>
  <p class="back-web">www.wattlebay.com.au</p>
</section>

<section class="card card--front" aria-label="Business card front">
  <div class="front-brand">
    <span class="front-brand__square"></span>
    <span class="front-brand__name">Wattlebay<br>Tourist Parks</span>
  </div>

  <span class="divider"></span>

  <div class="contact">
    <p class="contact__name">Neil Perrow</p>
    <p class="contact__role">Director</p>
    <ul class="contact__list">
      <li class="contact__item">
        <svg class="contact__icon" viewBox="0 0 24 24" aria-hidden="true">
          <path fill="var(--teal)" d="M6.6 10.8a15.1 15.1 0 0 0 6.6 6.6l2.2-2.2c.3-.3.7-.4 1-.2 1.1.4 2.3.6 3.6.6.6 0 1 .4 1 1V20c0 .6-.4 1-1 1A17 17 0 0 1 3 4c0-.6.4-1 1-1h3.5c.6 0 1 .4 1 1 0 1.3.2 2.5.6 3.6.1.3 0 .7-.2 1z"/>
        </svg>
        0491 570 156
      </li>
      <li class="contact__item">
        <svg class="contact__icon" viewBox="0 0 24 24" aria-hidden="true">
          <rect x="2" y="5" width="20" height="14" fill="var(--teal)"/>
          <path d="M2 5l10 8 10-8" fill="none" stroke="#fff" stroke-width="2"/>
        </svg>
        perrow@wattlebay.com.au
      </li>
    </ul>
  </div>

  <svg class="front-band" width="560" height="120" viewBox="0 0 560 120" aria-hidden="true">
    <polygon points="0,0 560,0 560,0 0,0" fill="none"/>
    <polygon points="0,30 300,30 300,38 0,38" fill="var(--teal)"/>
    <polygon points="0,44 300,44 300,120 0,120" fill="var(--teal-light)" opacity="0.35"/>
    <polygon points="0,120 0,44 300,44 300,120" fill="url(#bandFade)"/>
    <polygon points="270,120 310,70 560,70 560,120" fill="var(--teal)"/>
    <polygon points="300,30 308,30 262,86 254,86" fill="var(--teal)"/>
    <defs>
      <linearGradient id="bandFade" x1="0" y1="0" x2="0" y2="1">
        <stop offset="0" stop-color="#ffffff" stop-opacity="0.9"/>
        <stop offset="1" stop-color="#ffffff" stop-opacity="0.3"/>
      </linearGradient>
    </defs>
  </svg>
  <p class="front-web">www.wattlebay.com.au</p>
</section>

</body>
</html>
```